Theatre Company needs a Poster design for a world premiere of "The Lantern" Play.

We are premiering a play that celebrates community in rural and regional Australia . We need a poster for A3 and A5 size and an image that can be used in our email correspondence/webpage.

Attached is some ideas the producing theatre committee has come up with, a river runs through the town itself.

Town

```html
<!DOCTYPE html>
<html lang="en">
<head>
<meta charset="utf-8">
<title>The Lantern — Marrowbank Theatre Company</title>
<link rel="stylesheet" href="https://fonts.googleapis.com/css2?family=Oswald:wght@500&family=Berkshire+Swash&family=Courgette&display=swap">
<style>
  :root {
    --ink: #000000;
    --cream: #f3ead8;
    --sepia-deep: #1a1208;
    --sepia-mid: #5c4522;
    --sepia-warm: #a9864c;
    --sepia-glow: #f1dcaa;
  }
  html, body {
    margin: 0;
    padding: 0;
    overflow: hidden;
    background: var(--ink);
  }
  .poster {
    position: relative;
    width: 939px;
    height: 1200px;
    background: var(--ink);
    color: var(--cream);
    overflow: hidden;
  }
  .company {
    position: absolute;
    top: 22px;
    left: 0;
    width: 100%;
    margin: 0;
    text-align: center;
    font-family: "Oswald", sans-serif;
    font-weight: 500;
    font-size: 34px;
    letter-spacing: 3px;
    text-transform: uppercase;
  }
  .presents {
    position: absolute;
    top: 88px;
    left: 0;
    width: 100%;
    margin: 0;
    text-align: center;
    font-family: "Courgette", cursive;
    font-size: 30px;
    letter-spacing: 8px;
  }
  .scene {
    position: absolute;
    left: 117px;
    top: 222px;
    width: 705px;
    height: 740px;
    border-radius: 50%;
    background:
      radial-gradient(ellipse 60% 8% at 50% 36%, rgba(248,232,190,0.85), rgba(248,232,190,0) 100%),
      linear-gradient(180deg,
        var(--sepia-deep) 0%,
        var(--sepia-mid) 18%,
        var(--sepia-warm) 30%,
        var(--sepia-glow) 36%,
        #3a2a12 40%,
        #6e5530 50%,
        var(--sepia-warm) 58%,
        #4a3718 72%,
        var(--sepia-deep) 100%);
    box-shadow: inset 0 0 60px 30px var(--ink);
  }
  .title {
    position: absolute;
    top: 960px;
    left: 0;
    width: 100%;
    margin: 0;
    text-align: center;
    font-family: "Berkshire Swash", cursive;
    font-weight: 400;
    font-size: 122px;
    line-height: 1;
    color: #ffffff;
  }
  .credit {
    position: absolute;
    top: 1135px;
    left: 0;
    width: 100%;
    margin: 0;
    text-align: center;
    font-family: "Courgette", cursive;
    font-size: 26px;
    letter-spacing: 2px;
  }
  .credit .author {
    text-transform: uppercase;
    letter-spacing: 3px;
  }
</style>
</head>
<body>
  <main class="poster">
    <p class="company">Marrowbank Theatre Company</p>
    <p class="presents">Presents</p>
    <div class="scene" role="img" aria-label="Sepia photograph of a calm river winding between low wooded banks under a glowing evening sky"></div>
    <h1 class="title">The Lantern</h1>
    <p class="credit">Written by <span class="author">Tess Calloway</span></p>
  </main>
</body>
</html>
```